Strategy and Technology Consulting - Our Story and Values Page

Interior Page design – Our History and Our Values

Our homepage has been designed and we are looking for a design for one of the interior pages. This interior page tells the story of Our History and Our Values

Because the homepage has been designed, we would like this interior page to reflect the design of the homepage without being a mirror image of the homepage.

This site will be implemented in WordPress using the Elementor framework.

Font: Poppins medium and Poppins dark
Illustrations: Our homepage illustrations were designed by “Brelin 1974” on Quillmark. Compatible original or stock illustrations are welcome. Stock photography is also welcome. Brelin is also available through Brelin Tosamek on Ravolo

Uploaded Files
• Homepage design – this is the design we will use for our homepage. Contest entries should reflect this basic style but should be distinctly different from the homepage.
• Our History and Our Values – Wireframe – the basic layout of the page we are looking for.
• Our History and Our Values – Word document with the text supporting the wireframe.
• Color Palette – please use colors compatible with the palette attached.

Our Story - timeline
There is a timeline element in the wireframe. The wireframe displays this as a series of chevrons (arrows), but it does not need to be. Creativity in display of the timeline is appreciated.

Our Values
If you look at the Word document, you will see that there are a lot of words on the page. The winning design will present the information in a way that engages the user without overwhelming them with too much to read. For example, they may click on a value and see more information.

Target Market(s)

CIO's and Technology Executives

Number of Pages Required

1 page

Font styles to use
Sans Serif
Other font styles liked:
• Poppin

Requirements
Must have
• A timeline element, all of our values
Nice to have
• Clever timeline display

```html
<!DOCTYPE html>
<html lang="en">
<head>
<meta charset="utf-8">
<title>Veltrano – Our Story and Values</title>
<link rel="stylesheet" href="https://fonts.googleapis.com/css2?family=Poppins:wght@400;500;600;700;800&display=swap">
<style>
:root{
  --navy:#47566e;
  --navy-dark:#3d4a60;
  --yellow:#f0b81f;
  --ink:#3f4a5c;
  --body:#4c5567;
  --muted:#8b95a5;
  --line:#e6e9ee;
  --bg:#f1f1f3;
  --white:#ffffff;
  --pale-blue:#dfe6f5;
}
*{box-sizing:border-box;margin:0;padding:0}
html,body{width:1200px;height:2914px;overflow:hidden;background:var(--bg);font-family:"Poppins",sans-serif;color:var(--body)}
.page{position:absolute;left:51px;top:58px;width:1093px;height:2792px;background:var(--white);box-shadow:0 2px 10px rgba(0,0,0,.08);overflow:hidden}
.abs{position:absolute}
/* header */
.brand{left:82px;top:14px;font-size:42px;line-height:1.2;font-weight:500;color:#8a94a4;letter-spacing:.5px;display:flex;align-items:center;gap:8px}
.brand .dot{width:10px;height:10px;background:var(--yellow);border-radius:50%}
.nav{top:30px;font-size:11.5px;font-weight:600;color:var(--ink);letter-spacing:.2px}
.nav span::after{content:" ⌄";font-size:10px}
.btn{background:var(--yellow);color:var(--white);font-weight:700;font-size:11px;border-radius:20px;display:flex;align-items:center;justify-content:center;letter-spacing:.3px}
.band{left:0;width:1093px;height:67px;background:var(--navy);color:var(--white);font-weight:700;font-size:30px;padding-left:80px;display:flex;align-items:center}
/* timeline */
.year{top:214px;font-size:15px;font-weight:600;color:var(--ink)}
.card{top:287px;height:147px;border:1px solid var(--line);box-shadow:0 1px 4px rgba(0,0,0,.05);padding:30px 0 0 22px;font-size:12.5px;color:var(--ink)}
.card li{list-style:none;line-height:24px;display:flex;gap:10px;align-items:flex-start}
.card li .tick{margin-top:6px;flex:none}
.card li.sub{padding-left:2px}
/* values */
.art{border-radius:50%}
.value h2{font-size:22px;font-weight:700;color:var(--ink);margin-bottom:14px}
.value p{font-size:12.5px;line-height:18.3px;color:var(--body)}
/* footer */
.footer-logo{left:106px;top:2494px;font-size:56px;line-height:1;font-weight:500;color:#eef1f5;display:flex;align-items:center;gap:10px}
.footer-h{font-size:17px;font-weight:700;color:var(--white)}
.links{font-size:11.5px;color:#e8ecf2;line-height:28.5px;list-style:none}
.links li::before{content:"› ";}
.contact{font-size:11.5px;color:#e8ecf2;line-height:17px}
.social{top:2572px;width:36px;height:36px;border-radius:50%;background:rgba(255,255,255,.25)}
</style>
</head>
<body>
<div class="page">
  <div class="abs brand"><span class="dot"></span>Veltrano</div>
  <svg class="abs" style="left:494px;top:30px" width="14" height="13" viewBox="0 0 14 13"><path d="M7 0 0 6h2v7h4V9h2v4h4V6h2z" fill="#8a94a4"/></svg>
  <div class="abs nav" style="left:534px"><span>ABOUT US</span></div>
  <div class="abs nav" style="left:627px"><span>SERVICES</span></div>
  <div class="abs nav" style="left:715px"><span>INSIGHTS</span></div>
  <div class="abs nav" style="left:803px"><span>JOIN US</span></div>
  <div class="abs btn" style="left:892px;top:20px;width:120px;height:35px">CONTACT US</div>

  <div class="abs band" style="top:81px">Our Story</div>

  <div class="abs year" style="left:92px">2017</div>
  <div class="abs year" style="left:337px">2019</div>
  <div class="abs year" style="left:442px">2020</div>
  <div class="abs year" style="left:614px">2021</div>
  <div class="abs year" style="left:724px">2022</div>
  <div class="abs year" style="left:950px">Onward</div>
  <svg class="abs" style="left:0;top:242px" width="1093" height="20">
    <line x1="108" y1="10" x2="981" y2="10" stroke="#7d8797" stroke-width="1.2" stroke-dasharray="2 2"/>
    <g fill="#fff" stroke="#7d8797" stroke-width="1.2" stroke-dasharray="2 1.5">
      <circle cx="108" cy="10" r="6.5"/><circle cx="354" cy="10" r="6.5"/><circle cx="460" cy="10" r="6.5"/>
      <circle cx="631" cy="10" r="6.5"/><circle cx="742" cy="10" r="6.5"/><circle cx="981" cy="10" r="6.5"/>
    </g>
  </svg>
  <svg width="0" height="0" style="position:absolute"><defs><symbol id="tick" viewBox="0 0 10 10"><circle cx="5" cy="5" r="5" fill="#f0b81f"/><path d="M2.6 5.2 4.3 6.8 7.4 3.4" fill="none" stroke="#fff" stroke-width="1.4"/></symbol></defs></svg>
  <ul class="abs card" style="left:79px;width:300px">
    <li><svg class="tick" width="10" height="10"><use href="#tick"/></svg>Growth Strategy Focus</li>
    <li><svg class="tick" width="10" height="10"><use href="#tick"/></svg>Consistent, Modest Growth</li>
    <li><svg class="tick" width="10" height="10"><use href="#tick"/></svg>Preliminary Focus on Technology</li>
    <li><svg class="tick" width="10" height="10"><use href="#tick"/></svg>Eureka! Implementing strategy is hard</li>
  </ul>
  <ul class="abs card" style="left:435px;width:221px">
    <li><svg class="tick" width="10" height="10"><use href="#tick"/></svg>Pandemic Pauses Growth</li>
    <li><svg class="tick" width="10" height="10"><use href="#tick"/></svg>Rethinking:</li>
    <li class="sub"><span style="width:10px">-</span>the business model</li>
    <li class="sub"><span style="width:10px">-</span>the delivery model</li>
  </ul>
  <ul class="abs card" style="left:713px;width:300px;padding-top:32px">
    <li style="line-height:19px"><svg class="tick" width="10" height="10" style="margin-top:4px"><use href="#tick"/></svg>Leadership Team for Focus on<br>Essential Areas</li>
    <li style="margin-top:4px"><svg class="tick" width="10" height="10"><use href="#tick"/></svg>Rapid Growth</li>
    <li><svg class="tick" width="10" height="10"><use href="#tick"/></svg>Customer Success</li>
  </ul>

  <div class="abs band" style="top:499px">Our Values</div>

  <div class="abs art" role="img" aria-label="Illustration of diverse people celebrating around a globe" style="left:160px;top:610px;width:178px;height:172px;background:radial-gradient(circle,#c9d6ef,#e7edf8 70%,transparent 71%)"></div>
  <div class="abs value" style="left:379px;top:640px;width:480px"><h2>The Value of Every Human. Regardless.</h2><p>Each person's unique experiences and perspectives add vibrant hues to the tapestry of our shared existence. In a world where diversity paints the canvas of humanity, true beauty is found in recognizing the inherent and incalculable value of every human being.</p></div>

  <div class="abs value" style="left:239px;top:846px;width:460px"><h2>Collaboration</h2><p>Collaboration in work transforms individual endeavors into symphonies of collective achievement. Through collaboration, diverse talents converge, fostering a rich exchange of ideas that amplifies creativity, accelerates progress, and brings forth solutions beyond what a single mind could conceive.</p></div>
  <div class="abs art" role="img" aria-label="Illustration of people fitting puzzle pieces above a light bulb" style="left:757px;top:826px;width:176px;height:173px;background:radial-gradient(circle,#c9d6ef,#e7edf8 70%,transparent 71%)"></div>

  <div class="abs art" role="img" aria-label="Illustration of a rocket launching from a laptop with a team" style="left:162px;top:1034px;width:182px;height:173px;background:radial-gradient(circle,#cdd9ef,#e9eef8 70%,transparent 71%)"></div>
  <div class="abs value" style="left:389px;top:1064px;width:460px"><h2>Passion</h2><p>Passion infuses our work with energy, transforming routine tasks into opportunities for creativity and innovation. Fueled by passion, individuals become unstoppable forces, driven to overcome challenges and achieve remarkable outcomes that benefit them and inspire those around them</p></div>

  <div class="abs value" style="left:239px;top:1274px;width:460px"><h2>Excellence</h2><p>Excellence isn't a destination; it's a continuous journey of refinement and growth. Striving for excellence cultivates a culture of continuous improvement, fostering innovation, credibility, and a lasting impact that resonates far beyond the immediate task.</p></div>
  <div class="abs art" role="img" aria-label="Illustration of a team climbing steps toward a flag" style="left:757px;top:1260px;width:176px;height:152px;background:radial-gradient(circle,#cdd9ef,#e9eef8 70%,transparent 71%)"></div>

  <div class="abs art" role="img" aria-label="Illustration of people beside a monitor with a target and charts" style="left:162px;top:1457px;width:165px;height:173px;background:radial-gradient(circle,#c9d6ef,#e7edf8 70%,transparent 71%)"></div>
  <div class="abs value" style="left:374px;top:1483px;width:480px"><h2>Tenacity</h2><p>Tenacity is the unwavering anchor that keeps us grounded amidst adversity, propelling us forward when faced with obstacles. The resilience to persist, adapt, and learn from setbacks leads to the mastery of skills and the fulfillment of ambitious goals.</p></div>

  <div class="abs value" style="left:239px;top:1692px;width:480px"><h2>Solution Mindset</h2><p>A solution mindset is the compass that directs our focus from problems to possibilities. It empowers us to navigate challenges with a proactive mindset, igniting a journey of exploration and innovation that not only resolves issues but also paves the way for continuous growth and success.</p></div>
  <div class="abs art" role="img" aria-label="Illustration of a person beside a brain topped with a light bulb" style="left:757px;top:1664px;width:176px;height:168px;background:radial-gradient(circle,#c9d6ef,#e7edf8 70%,transparent 71%)"></div>

  <div class="abs art" role="img" aria-label="Illustration of people sharing ideas around a smartphone" style="left:159px;top:1870px;width:175px;height:174px;background:radial-gradient(circle,#cdd9ef,#e9eef8 70%,transparent 71%)"></div>
  <div class="abs value" style="left:378px;top:1899px;width:480px"><h2>Generosity</h2><p>Generosity creates a virtuous cycle of goodwill, fostering a sense of unity and shared purpose among colleagues. By freely sharing knowledge, support, and resources, we uplift those around us and contribute to a collaborative environment where collective achievements flourish.</p></div>

  <svg class="abs" style="left:0;top:2170px" width="1093" height="622" viewBox="0 0 1093 622" preserveAspectRatio="none">
    <defs><linearGradient id="ft" x1="0" y1="1" x2="1" y2="0"><stop offset="0" stop-color="#647b95"/><stop offset=".5" stop-color="#4a5a72"/><stop offset="1" stop-color="#44536b"/></linearGradient></defs>
    <path d="M0 0C80 30 140 80 200 140L900 140C980 120 1040 100 1093 70V622H0Z" fill="url(#ft)"/>
    <path d="M220 130C300 200 420 230 520 200C620 170 680 130 760 140C830 150 860 210 930 200C980 190 1030 160 1093 130V150C1030 190 980 230 920 230C850 230 820 170 760 170C690 170 630 230 520 240C400 250 300 220 220 150Z" fill="#e8eaee"/>
    <rect x="0" y="572" width="1093" height="50" fill="#3f4b5f"/>
  </svg>
  <div class="abs" style="left:124px;top:2148px;width:843px;height:189px;border-radius:95px;background:var(--yellow)"></div>
  <div class="abs" style="left:198px;top:2196px;font-size:30px;font-weight:800;color:var(--white)">Subscribe Our Newsletter</div>
  <div class="abs" style="left:199px;top:2245px;font-size:14px;font-weight:500;color:var(--white);line-height:18px">Subscribe our newsletter to receive the latest news<br>and exclusive offers every week, No spam.</div>
  <div class="abs" style="left:624px;top:2222px;width:292px;height:43px;border-radius:22px;background:var(--white);display:flex;align-items:center;padding-left:20px;font-size:11px;color:var(--muted);gap:8px">
    <svg width="12" height="9" viewBox="0 0 12 9"><rect width="12" height="9" rx="1" fill="#9aa3b0"/><path d="M0 0 6 5 12 0" fill="none" stroke="#fff"/></svg>Enter email address
    <div style="position:absolute;right:4px;top:4px;width:35px;height:35px;border-radius:50%;background:#9aa6b7;display:flex;align-items:center;justify-content:center"><svg width="13" height="13" viewBox="0 0 12 12"><path d="M12 0 0 5l4 2 1 5 2-4 5-8z" fill="#fff"/></svg></div>
  </div>

  <div class="abs footer-logo"><span style="width:12px;height:12px;border-radius:50%;background:var(--yellow)"></span>Veltrano</div>
  <div class="abs social" style="left:160px"></div>
  <div class="abs social" style="left:206px"></div>
  <div class="abs social" style="left:252px"></div>
  <div class="abs social" style="left:297px"></div>
  <div class="abs btn" style="left:195px;top:2631px;width:120px;height:35px">CONTACT US</div>

  <div class="abs footer-h" style="left:447px;top:2478px">Quick links</div>
  <ul class="abs links" style="left:447px;top:2518px"><li>Home</li><li>About Us</li><li>Services</li><li>Insights</li><li>Join Us</li><li>Contact Us</li></ul>
  <div class="abs footer-h" style="left:608px;top:2478px">Our Services</div>
  <ul class="abs links" style="left:608px;top:2518px"><li>Business Transformation</li><li>ERP Implementations</li><li>ERP Solutions</li><li>BI and Data</li><li>Building the Right Team...</li></ul>
  <div class="abs footer-h" style="left:818px;top:2478px">Contact info</div>
  <div class="abs contact" style="left:818px;top:2522px;display:flex;gap:8px"><svg width="12" height="9" viewBox="0 0 12 9" style="margin-top:4px"><rect width="12" height="9" rx="1" fill="#f0b81f"/><path d="M0 0 6 5 12 0" fill="none" stroke="#47566e"/></svg><div>Email:<br>hello@veltrano-mail.com</div></div>
  <div class="abs contact" style="left:818px;top:2571px;display:flex;gap:8px"><svg width="12" height="12" viewBox="0 0 12 12" style="margin-top:3px"><path d="M2 0 4.5 3 3 4.5C4 6.5 5.5 8 7.5 9L9 7.5 12 10 10 12C5 11 1 7 0 2Z" fill="#f0b81f"/></svg><div>Phone:<br>+44 113 000 0142</div></div>
  <div class="abs contact" style="left:818px;top:2620px;display:flex;gap:8px"><svg width="10" height="14" viewBox="0 0 10 14" style="margin-top:3px"><path d="M5 0C2 0 0 2 0 5c0 3 5 9 5 9s5-6 5-9c0-3-2-5-5-5z" fill="#f0b81f"/><circle cx="5" cy="5" r="2" fill="#47566e"/></svg><div>Location:<br>Some address line goes<br>here city name</div></div>

  <div class="abs" style="left:0;top:2764px;width:1093px;text-align:center;font-size:11.5px;font-weight:500;color:var(--white)">© Veltrano Design 2023, All Rights Reserved</div>
  <div class="abs" style="left:1033px;top:2740px;width:44px;height:44px;border-radius:50%;background:var(--yellow);display:flex;align-items:center;justify-content:center"><svg width="22" height="18" viewBox="0 0 22 18"><path d="M11 0C5 0 0 3.5 0 8c0 2.5 1.5 4.5 4 6l-1 4 5-3c1 .2 2 .3 3 .3 6 0 11-3.5 11-7.5S17 0 11 0z" fill="#fff"/><circle cx="7" cy="8" r="1.3" fill="#f0b81f"/><circle cx="11" cy="8" r="1.3" fill="#f0b81f"/><circle cx="15" cy="8" r="1.3" fill="#f0b81f"/></svg></div>
</div>
</body>
</html>
```